OrvanoGoodsHub.com -Ecommerce Website for Luxury Products

This will be an ecommerce site. A website portal that will allow both consumers to enter one way and see specific purchase options and businesses to enter via a different link that allows B2B to see their specific options once logged into. B2C can purchase both as a guest/or after account is setup. B2B must be approved to set up account. This is front end website project. Back-end integration is separate. Will be hosted on Servantia with a domain registration held at Pexadrinet. Additional website concept/idea/synergy can be found from sister site-KRWZHospitality.com

```html
<!DOCTYPE html>
<html lang="en">
<head>
<meta charset="utf-8">
<title>Orvano Goods — Curated Luxury for Connoisseurs</title>
<link href="https://fonts.googleapis.com/css2?family=Playfair+Display:wght@400;500;600&family=Poppins:wght@300;400;500&display=swap" rel="stylesheet">
<style>
:root{
  --bg:#0a0a0a;
  --bg-soft:#141210;
  --gold:#a8845a;
  --gold-light:#c7a377;
  --text:#e9e4dc;
  --muted:#a9a39a;
  --line:#2a2622;
  --serif:'Playfair Display', Georgia, serif;
  --sans:'Poppins', Arial, sans-serif;
}
*{box-sizing:border-box;margin:0;padding:0}
html,body{width:1200px;height:3824px;overflow:hidden;background:var(--bg);color:var(--text);font-family:var(--sans)}
.page{position:relative;width:1200px;height:3824px}
.btn{display:inline-block;background:var(--gold);color:#1a140d;font-size:13px;padding:10px 22px;border-radius:22px;font-family:var(--sans);font-weight:500}
.btn-ghost{background:transparent;border:1px solid var(--gold-light);color:var(--text)}

/* Header + hero */
.hero{position:absolute;top:0;left:0;width:1200px;height:760px;background:radial-gradient(ellipse at 50% 75%,#3a2a1c 0%,#1b1510 40%,#0b0a09 80%);}
.hero-photo{position:absolute;left:0;right:0;bottom:0;height:340px;background:linear-gradient(90deg,#2a1a0f 0%,#5a3a22 20%,#1c1410 50%,#5a3a22 80%,#2a1a0f 100%);opacity:.75}
.nav{position:absolute;top:24px;left:60px;right:60px;height:80px;border:1px solid rgba(199,163,119,.35);border-radius:40px;background:rgba(10,10,10,.7);display:flex;align-items:center;padding:0 28px}
.brand{display:flex;align-items:center;gap:10px;font-family:var(--serif);font-size:20px;letter-spacing:2px;color:var(--text)}
.brand-mark{width:14px;height:14px;background:var(--gold)}
.nav-links{display:flex;gap:30px;margin-left:auto;margin-right:30px;font-size:13px;color:var(--text)}
.nav-icons{display:flex;gap:14px;margin-left:20px}
.nav-icons svg{width:20px;height:20px}
.hero-copy{position:absolute;top:250px;left:0;width:1200px;text-align:center}
.hero-copy h1{font-family:var(--serif);font-weight:500;font-size:52px;line-height:1.15}
.hero-copy p{margin:18px auto 0;width:520px;font-size:14px;color:var(--text);line-height:1.5}
.hero-actions{margin-top:26px;display:flex;justify-content:center;gap:16px}
.scroll-dot{position:absolute;left:588px;top:700px;width:24px;height:36px;border-radius:12px;background:var(--gold)}

/* Intro */
.intro{position:absolute;top:820px;left:160px;width:880px;height:340px;display:flex;gap:60px;align-items:center}
.intro-photo{width:520px;height:340px;background:linear-gradient(135deg,#3b2414,#7a4a26 50%,#2a1a10);border-radius:4px}
.section-title{font-family:var(--serif);font-weight:500;font-size:32px;color:var(--text)}
.intro-text p{font-size:12px;line-height:1.6;color:var(--muted);margin-top:14px}
.intro-text ul{list-style:none;margin-top:14px}
.intro-text li{font-size:12px;color:var(--muted);padding-left:16px;position:relative;margin-bottom:8px}
.intro-text li::before{content:"";position:absolute;left:0;top:6px;width:6px;height:6px;border-radius:50%;background:var(--gold)}
.intro-text .btn{margin-top:10px}

/* Collections */
.collections{position:absolute;top:1240px;left:0;width:1200px;text-align:center}
.collections .lead{font-size:13px;color:var(--muted);margin-top:10px}
.cards{display:flex;gap:20px;justify-content:center;margin-top:40px}
.card{width:232px;height:380px;border-radius:6px;position:relative;overflow:hidden}
.card span{position:absolute;bottom:22px;left:0;right:0;font-family:var(--serif);font-size:18px;color:var(--text)}
.c1{background:linear-gradient(180deg,#2a1a10,#6b4022 60%,#1a120c)}
.c2{background:linear-gradient(180deg,#3a2a1c,#8a6a44 55%,#1c140e)}
.c3{background:linear-gradient(180deg,#1a1614,#3a302a 55%,#0e0c0a)}
.c4{background:linear-gradient(180deg,#4a2a14,#a0622e 55%,#2a180c)}
.collections .btn{margin-top:48px}

/* Lounges */
.lounges{position:absolute;top:1900px;left:0;width:1200px;height:460px;background:radial-gradient(ellipse at 50% 30%,#2a2622 0%,#121110 55%,#0a0a0a 100%);text-align:center;padding-top:110px}
.lounges p{width:620px;margin:14px auto 0;font-size:12px;line-height:1.6;color:var(--muted)}
.lounges .btn{margin-top:22px}
.lounge-photo{position:absolute;left:300px;top:320px;width:600px;height:60px;border-radius:30px;background:linear-gradient(90deg,#1a100a,#6a3e1e 40%,#8a5a2e 60%,#1a100a)}

/* Division */
.division{position:absolute;top:2400px;left:160px;width:880px;height:420px;display:flex;justify-content:space-between;align-items:center}
.division-text{width:300px}
.division-text p{font-size:12px;line-height:1.6;color:var(--muted);margin:16px 0 20px}
.division-photo{width:520px;height:420px;border-radius:4px;background:linear-gradient(135deg,#1c1814,#4a3a2a 45%,#6a4a2e 70%,#1a1410)}

/* Partners */
.partners{position:absolute;top:2860px;left:0;width:1200px;display:flex;justify-content:center;gap:56px}
.partners svg{width:130px;height:130px}
.dots{position:absolute;top:3034px;left:0;width:1200px;display:flex;justify-content:center;gap:8px}
.dots i{width:8px;height:8px;border-radius:50%;background:#444}
.dots i.on{background:var(--gold)}

/* Concierge */
.concierge{position:absolute;top:3140px;left:272px;width:656px;height:300px;background:linear-gradient(180deg,#a8845a,#8c6a44);border-radius:10px;text-align:center;padding-top:90px}
.concierge h2{font-family:var(--serif);font-weight:500;font-size:36px;color:#fff}
.concierge p{font-size:12px;color:#f3e8da;margin-top:8px;line-height:1.5}
.concierge .btn{margin-top:16px;background:#1a140d;color:var(--text)}

/* Footer */
.footer{position:absolute;top:3520px;left:0;width:1200px;height:304px;background:#0d0c0b;border-top:1px solid var(--line)}
.footer-cols{display:flex;padding:56px 0 0 120px;gap:0}
.footer-brand{width:228px}
.footer-brand .brand{font-size:22px}
.footer-brand p{font-size:11px;color:var(--muted);margin-top:10px}
.footer-col{width:228px}
.footer-col h3{font-family:var(--serif);font-weight:500;font-size:22px;margin-bottom:12px}
.footer-col a{display:block;font-size:12px;color:var(--muted);margin-bottom:6px;text-decoration:none}
.social{display:flex;gap:10px}
.social i{width:26px;height:26px;border-radius:50%;background:#2a2622;display:block}
.footer-bottom{position:absolute;bottom:0;left:0;right:0;height:56px;border-top:1px solid var(--line);text-align:center;line-height:56px;font-size:11px;color:var(--muted)}
.to-top{position:absolute;right:24px;bottom:60px;width:36px;height:36px;border-radius:50%;background:var(--gold)}
</style>
</head>
<body>
<div class="page">

<section class="hero">
  <div class="hero-photo" role="img" aria-label="Dark lounge with two leather chesterfield armchairs"></div>
  <nav class="nav">
    <div class="brand"><span class="brand-mark"></span>ORVANO GOODS</div>
    <div class="nav-links"><span>Home</span><span>About</span><span>Retail</span><span>Wholesale Portal</span><span>Partner Showcase</span></div>
    <span class="btn">Contact Us</span>
    <div class="nav-icons">
      <svg viewBox="0 0 24 24" fill="none" stroke="#e9e4dc" stroke-width="1.5"><circle cx="12" cy="8" r="4"/><path d="M4 21c1-4 4-6 8-6s7 2 8 6"/></svg>
      <svg viewBox="0 0 24 24" fill="none" stroke="#e9e4dc" stroke-width="1.5"><path d="M12 20s-7-4.5-7-10a4 4 0 0 1 7-2.5A4 4 0 0 1 19 10c0 5.5-7 10-7 10z"/></svg>
      <svg viewBox="0 0 24 24" fill="none" stroke="#e9e4dc" stroke-width="1.5"><path d="M3 4h3l2 11h11l2-8H7"/><circle cx="9" cy="19" r="1.5"/><circle cx="18" cy="19" r="1.5"/></svg>
    </div>
  </nav>
  <div class="hero-copy">
    <h1>Curated Luxury for Connoisseurs.<br>Crafted for Lounges.</h1>
    <p>Discover exclusive lifestyle accoutrements designed to elevate your personal indulgence and professional hospitality spaces.</p>
    <div class="hero-actions"><span class="btn">Shop Collection</span><span class="btn btn-ghost">Request Access</span></div>
  </div>
  <div class="scroll-dot"></div>
</section>

<section class="intro">
  <div class="intro-photo" role="img" aria-label="Cigars resting in a wooden presentation box"></div>
  <div class="intro-text">
    <h2 class="section-title">Purveyors of Distinction</h2>
    <p>Orvano Goods, a division of KRWZ Hospitality, is dedicated to crafting unparalleled luxury experiences. Our dual approach serves both the discerning individual and sophisticated hospitality venues.</p>
    <ul>
      <li>Exclusive, curated selections for personal &amp; professional indulgence.</li>
      <li>Partnerships with luxury lounges across the globe.</li>
      <li>Commitment to craftsmanship and timeless elegance.</li>
    </ul>
    <span class="btn">Read More</span>
  </div>
</section>

<section class="collections">
  <h2 class="section-title">Explore Our Signature Collections</h2>
  <p class="lead">Handpicked items for personal indulgence or to enhance your lounge experience.</p>
  <div class="cards">
    <div class="card c1" role="img" aria-label="Cigar accessories on a lounge table"><span>Cigar Accessories</span></div>
    <div class="card c2" role="img" aria-label="Fragrance bottles and oils"><span>Fragrances &amp; Oils</span></div>
    <div class="card c3" role="img" aria-label="Featured artisan portrait in dark studio"><span>Artists &amp; Accessories</span></div>
    <div class="card c4" role="img" aria-label="Special edition humidor set"><span>Special Edition Sets</span></div>
  </div>
  <span class="btn">Inquire for Wholesale</span>
</section>

<section class="lounges">
  <h2 class="section-title">Crafted for Lounges &amp; Luxury Venues</h2>
  <p>We partner with lounges, hospitality brands, and boutique retailers who share our commitment to quality and elevated experiences.</p>
  <p>Orvano Goods wholesale partners gain access to exclusive products, premium pricing, and collections designed to enhance brand perception and customer loyalty.</p>
  <span class="btn">Apply for Wholesale Access</span>
  <div class="lounge-photo" role="img" aria-label="Single cigar amid drifting smoke and tobacco leaves"></div>
</section>

<section class="division">
  <div class="division-text">
    <h2 class="section-title">A Division<br>of KRWZ Hospitality</h2>
    <p>Backed by the experience and vision of KRWZ Hospitality, Orvano Goods blends hospitality expertise with luxury retail, ensuring products that perform as beautifully as they present.</p>
    <span class="btn">Read More</span>
  </div>
  <div class="division-photo" role="img" aria-label="Private lounge with leather armchairs and bookshelves"></div>
</section>

<div class="partners">
  <svg viewBox="0 0 100 100"><polygon points="50,4 90,27 90,73 50,96 10,73 10,27" fill="#1e1c1a" stroke="#3a3632"/></svg>
  <svg viewBox="0 0 100 100"><polygon points="50,4 90,27 90,73 50,96 10,73 10,27" fill="#1e1c1a" stroke="#3a3632"/></svg>
  <svg viewBox="0 0 100 100"><polygon points="50,4 90,27 90,73 50,96 10,73 10,27" fill="#1e1c1a" stroke="#3a3632"/></svg>
  <svg viewBox="0 0 100 100"><polygon points="50,4 90,27 90,73 50,96 10,73 10,27" fill="#1e1c1a" stroke="#3a3632"/></svg>
  <svg viewBox="0 0 100 100"><polygon points="50,4 90,27 90,73 50,96 10,73 10,27" fill="#1e1c1a" stroke="#3a3632"/></svg>
</div>
<div class="dots"><i class="on"></i><i></i><i></i></div>

<section class="concierge">
  <h2>Concierge Level Service</h2>
  <p>Have a question, custom request, or wholesale inquiry?<br>Our concierge team is here to assist with personalized support and tailored solutions.</p>
  <span class="btn">Contact Orders &amp; Inquiries</span>
</section>

<footer class="footer">
  <div class="footer-cols">
    <div class="footer-brand">
      <div class="brand"><span class="brand-mark"></span>ORVANO GOODS</div>
      <p>The house of luxury lifestyle accoutrements</p>
    </div>
    <div class="footer-col"><h3>Explore</h3><a>Retail Collections</a><a>Wholesale Portal</a><a>Partner Showcase</a><a>About Us</a></div>
    <div class="footer-col"><h3>Support</h3><a>Contact &amp; Concierge</a><a>Wholesale Inquiries</a><a>Custom Orders</a></div>
    <div class="footer-col"><h3>Legal</h3><a>Privacy Policy</a><a>Terms &amp; Conditions</a><a>Disclaimer</a></div>
    <div class="footer-col"><h3>Follow</h3><div class="social"><i></i><i></i><i></i></div></div>
  </div>
  <span class="to-top"></span>
  <div class="footer-bottom">© 2026 OrvanoGoodsHub.com. All Rights Reserved.</div>
</footer>

</div>
</body>
</html>
```